Professional Services - letterhead / business cards

The company (velmora partners) will provide services to Investment Funds and large investors in Spain. I have recently chosen a logo that I am attaching.

I would like a simple stationary design that i could use as letter head, business cards and "with compliments" cards.

I am not quite sure which color I will mostly use for the logo, in the email signature I will probably lean towards the white background and grey letters. I am attaching my favourite options.

Target Market(s)

Large Multinationals, Investment funds and Law firms

Industry/Entity Type

Business

Requirements
Must have
• my details are:
Luis R. Abadal
Velmora Partners S.L.
Casa de Torrelumbre
Calle de Vientoalto 27
28014 Madrid
T: +34 (91) 387-2265
M: +34 (646) 819-054
e-mail: labadal@velmorapartners.com

```html
<!DOCTYPE html>
<html lang="en">
<head>
<meta charset="utf-8">
<title>Velmora Partners – Business Card</title>
<link rel="stylesheet" href="https://fonts.googleapis.com/css2?family=Mulish:wght@400;700&display=swap">
<style>
  :root {
    --navy: #27286b;
    --grey: #a7a8ad;
    --text-grey: #6b6c72;
    --white: #ffffff;
    --backdrop: #ecebe8;
  }
  * { box-sizing: border-box; margin: 0; padding: 0; }
  html, body {
    width: 1200px; height: 711px; overflow: hidden;
    background: var(--backdrop);
    font-family: "Mulish", sans-serif;
  }
  .stage { position: relative; width: 1200px; height: 711px; }
  .card {
    position: absolute; width: 540px; height: 310px;
    overflow: hidden;
    box-shadow: 0 6px 18px rgba(0,0,0,.18);
  }
  .card--front { left: 45px; top: 200px; background: var(--white); }
  .card--back { left: 615px; top: 200px; background: var(--navy); }

  .wordmark {
    position: absolute; font-weight: 400; letter-spacing: .5px;
    white-space: nowrap;
  }
  .card--front .wordmark { left: 50px; top: 38px; font-size: 46px; color: var(--navy); }
  .card--back .wordmark { left: 0; right: 0; top: 100px; text-align: center; font-size: 46px; color: var(--white); }

  .address {
    position: absolute; left: 40px; top: 118px;
    font-size: 13px; color: var(--text-grey); letter-spacing: .2px;
    white-space: nowrap;
  }
  .swoosh { position: absolute; left: 0; top: 0; }

  .holder { position: absolute; left: 34px; top: 262px; color: var(--white); }
  .holder__name { font-weight: 700; font-size: 19px; letter-spacing: .5px; line-height: 22px; }
  .holder__company { font-size: 12px; margin-top: 1px; }

  .divider {
    position: absolute; left: 222px; top: 212px;
    width: 1px; height: 66px; background: var(--white);
  }
  .contacts {
    position: absolute; left: 238px; top: 210px;
    list-style: none; color: var(--white); font-size: 13px;
  }
  .contacts li { display: flex; align-items: center; gap: 8px; height: 22px; }
  .contacts svg { width: 11px; height: 11px; flex: none; }

  .website {
    position: absolute; left: 0; right: 0; bottom: 48px;
    text-align: center; color: var(--white);
    font-size: 13px; font-weight: 700; letter-spacing: 7px;
  }
</style>
</head>
<body>
<main class="stage">
  <section class="card card--front" aria-label="Business card front">
    <div class="wordmark">velmora partners</div>
    <p class="address">Casa de Torrelumbre, Calle de Vientoalto 27, 28014 Madrid</p>
    <svg class="swoosh" width="540" height="310" viewBox="0 0 540 310" aria-hidden="true">
      <path d="M0,252 Q240,165 540,150 L540,162 Q240,176 0,264 Z" fill="var(--grey)"/>
      <path d="M0,310 L0,268 Q240,181 540,166 L540,310 Z" fill="var(--navy)"/>
    </svg>
    <div class="holder">
      <div class="holder__name">Luis R. Abadal</div>
      <div class="holder__company">Velmora Partners S.L.</div>
    </div>
    <div class="divider"></div>
    <ul class="contacts">
      <li>
        <svg viewBox="0 0 12 12" aria-hidden="true"><path d="M2.5,1 L4.5,1 L5.2,3.6 L4,4.6 Q5,7 7.4,8 L8.4,6.8 L11,7.5 L11,9.5 Q10.5,11 9,11 Q1,10 1,3 Q1,1.5 2.5,1 Z" fill="var(--white)"/></svg>
        +34 (91) 387-2265
      </li>
      <li>
        <svg viewBox="0 0 12 12" aria-hidden="true"><rect x="3" y="0.5" width="6" height="11" rx="1" fill="var(--white)"/><rect x="4" y="2" width="4" height="6" fill="var(--navy)"/></svg>
        +34 (646) 819-054
      </li>
      <li>
        <svg viewBox="0 0 12 12" aria-hidden="true"><rect x="0.5" y="2.5" width="11" height="7.5" rx="1" fill="var(--white)"/><path d="M1,3 L6,7 L11,3" fill="none" stroke="var(--navy)" stroke-width="1"/></svg>
        labadal@velmorapartners.com
      </li>
    </ul>
  </section>

  <section class="card card--back" aria-label="Business card back">
    <div class="wordmark">velmora partners</div>
    <p class="website">www.velmorapartners.com</p>
  </section>
</main>
</body>
</html>
```